Business Card Design Project - 2 sided

We need a business card design for a card having one business on each side (ie. two businesses on one card). Would like a design that incorporates logo, tagline and normal fields (name, position, address, phone).

Would also like an allowance for small font text along the bottom (text to be determined, but less than 50 characters).

NB. Attached logo for Harbor Quill has two variations - either can be used.

www.harborquill-example.com / www.velmaro-example.com

```html
<!DOCTYPE html>
<html lang="en">
<head>
<meta charset="utf-8">
<title>Harbor Quill / Velmaro Business Card</title>
<link rel="stylesheet" href="https://fonts.googleapis.com/css2?family=Open+Sans:wght@400;600;700&display=swap">
<style>
  :root {
    --backdrop: #4b2c1b;
    --card-white: #ffffff;
    --navy: #262463;
    --navy-text: #2b2a6b;
    --green: #8cbf45;
    --green-light: #a4cf5c;
    --green-dark: #72a33a;
    --blue: #2a86c8;
    --divider-blue: #3a7cc0;
    --ink: #333333;
    --panel-text: #ffffff;
  }
  * { box-sizing: border-box; margin: 0; padding: 0; }
  html, body {
    width: 1200px; height: 412px; overflow: hidden;
    background: var(--backdrop);
    font-family: "Open Sans", Arial, sans-serif;
  }
  .canvas { position: relative; width: 1200px; height: 412px; }
  .card {
    position: absolute; top: 64px; width: 497px; height: 284px;
    background: var(--card-white); display: flex;
  }
  .card--harbor { left: 75px; }
  .card--velmaro { left: 629px; }

  .brand-side {
    position: relative; width: 272px; height: 100%;
    display: flex; flex-direction: column; align-items: center; justify-content: center;
  }
  .divider { width: 4px; height: 100%; }
  .card--harbor .divider { background: var(--green); }
  .card--velmaro .divider { background: var(--divider-blue); }

  .brand-name {
    display: flex; align-items: center; gap: 10px;
    font-weight: 600; white-space: nowrap;
  }
  .brand-mark { width: 18px; height: 18px; border-radius: 50%; flex: none; }

  .card--harbor .brand-name { font-size: 25px; color: var(--navy-text); letter-spacing: 1px; margin-top: 44px; }
  .card--harbor .brand-mark { background: var(--green); }
  .card--harbor .tagline { font-size: 10px; color: var(--ink); margin-top: 6px; }

  .card--velmaro .brand-name { font-size: 40px; color: var(--blue); }
  .card--velmaro .brand-mark { background: var(--green); width: 26px; height: 26px; }
  .card--velmaro .tagline { font-size: 14px; font-weight: 700; color: var(--ink); margin-top: 2px; }

  .contact-panel {
    flex: 1; height: 100%; color: var(--panel-text);
    padding: 45px 0 0 27px; font-size: 13px; line-height: 17px;
  }
  .card--harbor .contact-panel { background: var(--navy); }
  .card--velmaro .contact-panel {
    background: linear-gradient(90deg, var(--green-light), var(--green-dark));
  }
  .person { font-size: 17px; font-weight: 700; margin-bottom: 14px; }
  .person .title { font-size: 13px; font-weight: 400; }
  .contact-list { list-style: none; }
  .contact-list li { display: flex; align-items: center; gap: 5px; }
  .contact-list svg { width: 10px; height: 10px; fill: var(--panel-text); flex: none; }
  .address { margin-top: 9px; }
  .fine-print { margin-top: 12px; font-size: 11px; line-height: 15px; letter-spacing: 0.2px; }
</style>
</head>
<body>
<main class="canvas">

  <section class="card card--harbor">
    <div class="brand-side">
      <div class="brand-name"><span class="brand-mark"></span>Harbor Quill</div>
      <p class="tagline">Website Translation and Localisation Specialist...</p>
    </div>
    <div class="divider"></div>
    <div class="contact-panel">
      <p class="person">Your Name <span class="title">/ Title</span></p>
      <ul class="contact-list">
        <li><svg viewBox="0 0 10 10"><path d="M2 0.5 L4 2.5 L3 4 Q4.5 6 6 7 L7.5 6 L9.5 8 L8 9.5 Q3 9 0.5 2 Z"/></svg>123-456-7890</li>
        <li><svg viewBox="0 0 10 10"><rect x="2.5" y="0" width="5" height="10" rx="1"/></svg>123-456-7890</li>
        <li><svg viewBox="0 0 10 10"><rect x="0" y="4" width="10" height="5" rx="1"/><rect x="2" y="0.5" width="6" height="3"/></svg>123-456-7890</li>
        <li><svg viewBox="0 0 10 10"><path d="M0 2 H10 V9 H0 Z M0 2 L5 6 L10 2"/></svg>name@website.com</li>
        <li><svg viewBox="0 0 10 10"><circle cx="5" cy="5" r="5"/></svg>www.website.com</li>
      </ul>
      <p class="address">Complex name, Street name<br>City, State, zip code</p>
      <p class="fine-print">xxxxxxxxxxxxxxxxxxxxxxxxxx<br>xxxxxxxxxxxxxxxxxxxxxxxxxx</p>
    </div>
  </section>

  <section class="card card--velmaro">
    <div class="brand-side">
      <div class="brand-name"><span class="brand-mark"></span>Velmaro</div>
      <p class="tagline">Professional SEO Services</p>
    </div>
    <div class="divider"></div>
    <div class="contact-panel">
      <p class="person">Your Name <span class="title">/ Title</span></p>
      <ul class="contact-list">
        <li><svg viewBox="0 0 10 10"><path d="M2 0.5 L4 2.5 L3 4 Q4.5 6 6 7 L7.5 6 L9.5 8 L8 9.5 Q3 9 0.5 2 Z"/></svg>123-456-7890</li>
        <li><svg viewBox="0 0 10 10"><rect x="2.5" y="0" width="5" height="10" rx="1"/></svg>123-456-7890</li>
        <li><svg viewBox="0 0 10 10"><rect x="0" y="4" width="10" height="5" rx="1"/><rect x="2" y="0.5" width="6" height="3"/></svg>123-456-7890</li>
        <li><svg viewBox="0 0 10 10"><path d="M0 2 H10 V9 H0 Z M0 2 L5 6 L10 2"/></svg>name@website.com</li>
        <li><svg viewBox="0 0 10 10"><circle cx="5" cy="5" r="5"/></svg>www.website.com</li>
      </ul>
      <p class="address">Complex name, Street name<br>City, State, zip code</p>
      <p class="fine-print">xxxxxxxxxxxxxxxxxxxxxxxxxx<br>xxxxxxxxxxxxxxxxxxxxxxxxxx</p>
    </div>
  </section>

</main>
</body>
</html>
```